Residential building / Apartments for sale landing page

I need a website / landing page design for my latest development project - a residential building with 70+ apartments for sale. I need the design in layers in Photoshop/Illustrator/InDesign format with all the icons/shapes/maps/graphic assets in vector format (svg, ai, eps) as much as possible.

I prefer white website and please consider the performance/coding experience. We're not making something suitable only for a design contest with fancy parallax effects and confusing animations. We're trying to create usable and clean UI with good UX.

The website will be custom coded, i.e. I'm not using WordPress.

I know that the existing 3D photos are not good but for now you can use them or replace them with some stock photos. I'm going to create new 3D photos soon.

Real Estate Development

1 page

```html
<!DOCTYPE html>
<html lang="en">
<head>
<meta charset="utf-8">
<title>High Grove – Landing Page Presentation</title>
<link href="https://fonts.googleapis.com/css2?family=Poppins:wght@300;400;500;600;700;800&display=swap" rel="stylesheet">
<style>
:root{
  --green:#8cc63f;
  --green-dark:#76b02c;
  --green-light:#a8d670;
  --green-pale:#bfe08f;
  --ink:#1c1c1c;
  --dark:#211f20;
  --muted:#7a7a7a;
  --soft:#f1f1f1;
  --line:#e2e2e2;
  --white:#ffffff;
}
*{box-sizing:border-box;margin:0;padding:0}
html,body{width:1200px;height:2187px;overflow:hidden;background:var(--green)}
body{font-family:'Poppins',sans-serif;color:var(--ink)}
.board{position:absolute;left:0;top:0;width:1413px;height:2576px;transform:scale(.84926);transform-origin:0 0;background:var(--green);overflow:hidden}
.board-waves{position:absolute;left:0;top:0}
.brand{position:absolute;left:0;width:1413px;top:245px;text-align:center;color:var(--white);font-weight:700;font-size:104px;letter-spacing:2px;line-height:1}
.brand-rule{position:absolute;left:433px;top:350px;width:526px;height:7px;background:var(--white)}
.board-label{position:absolute;top:444px;color:var(--white);font-weight:700;font-size:26px;letter-spacing:.5px}

/* page mockup */
.site{position:absolute;top:482px;width:447px;height:1973px;background:var(--white);overflow:hidden;box-shadow:0 10px 30px rgba(0,0,0,.15)}
.site > *{position:absolute}
.nav{left:0;top:0;width:447px;height:35px;background:var(--white)}
.nav-logo{position:absolute;left:33px;top:12px;font-weight:700;font-size:7.5px;color:var(--ink)}
.nav-menu{position:absolute;left:146px;top:14px;display:flex;gap:10px;font-size:4.2px;font-weight:500;list-style:none;align-items:center}
.nav-menu .is-cta{background:#e6e6e6;padding:3px 7px}
.hero{left:0;top:35px;width:447px;height:231px;background:var(--soft)}
.hero-panel{left:281px;top:35px;width:166px;height:120px;background:var(--green)}
.hero-photo{left:262px;top:56px;width:185px;height:210px;background:linear-gradient(160deg,#5f7a4d,#c9d2c0 55%,#4f6b3d)}
.hero-title{left:33px;top:94px;font-size:16px;line-height:20px;font-weight:400}
.hero-title b{color:var(--green);font-weight:700}
.hero-price{left:33px;top:160px;font-size:7px}
.btn-dark{left:33px;top:182px;width:56px;height:17px;background:var(--ink);color:var(--white);font-size:4.5px;font-weight:700;display:flex;align-items:center;justify-content:center;gap:3px}
.project-art{left:33px;top:288px;width:181px;height:196px;background:linear-gradient(150deg,#6e8f57,#e9ece6 55%,#7a9a62)}
.project-title{left:249px;top:362px;font-size:17px;line-height:20px}
.project-title b{font-weight:700}
.accent{height:1.5px;width:28px;background:var(--green)}
.project-accent{left:249px;top:406px}
.project-text{left:249px;top:416px;width:165px;font-size:5.3px;line-height:10px;color:var(--muted);font-weight:300}
.sec-title{left:0;width:447px;text-align:center;font-size:15.5px;font-weight:400}
.sec-title b{font-weight:700}
.sec-accent{left:212px;width:22px;height:1.5px;background:var(--green)}
.sec-sub{left:40px;width:367px;text-align:center;font-size:5.3px;color:#555;line-height:8px}
.arrow-btn{width:9px;height:9px;border-radius:50%;background:#e8e8e8;font-size:5px;display:flex;align-items:center;justify-content:center;color:#777}

.apt-card{top:575px;width:122px;height:180px;background:var(--white);box-shadow:0 3px 10px rgba(0,0,0,.12)}
.apt-card > *{position:absolute}
.apt-photo{left:0;top:0;width:122px;height:90px;background:linear-gradient(150deg,#4f6e3e,#c7d0c2 50%,#5d7d49)}
.apt-tag{left:9px;top:12px;background:var(--green);color:var(--white);font-size:3.5px;font-weight:700;padding:1px 3px}
.apt-price{right:0;top:75px;width:46px;height:14px;background:var(--green);color:var(--white);font-size:7px;font-weight:600;display:flex;align-items:center;justify-content:center}
.apt-status{left:9px;top:94px;background:#eee;font-size:3.5px;padding:1px 4px;font-weight:500}
.apt-name{left:9px;top:104px;font-size:7px;font-weight:500}
.apt-desc{left:9px;top:117px;width:104px;font-size:4.4px;line-height:7px;color:var(--muted)}
.apt-specs{left:9px;top:147px;display:flex;gap:8px;font-size:3.8px;color:#666}
.apt-view{left:9px;top:158px;font-size:8.5px;font-weight:500;border-bottom:1px solid #ccc;padding-right:10px}

.layout-note{left:0;width:447px;top:788px;text-align:center;font-size:6px}
.fac-card{top:873px;width:90px;height:110px;background:var(--white);box-shadow:0 3px 10px rgba(0,0,0,.1);z-index:2;padding:14px 10px}
.fac-card svg{display:block;width:20px;height:20px}
.fac-card h4{margin-top:12px;font-size:6.5px;font-weight:600}
.fac-card p{margin-top:4px;font-size:4.4px;line-height:7.5px;color:var(--muted)}
.fac-card span{display:block;margin-top:5px;font-size:8px;color:#aaa}
.fac-card.is-active{background:var(--green);color:var(--white)}
.fac-card.is-active p,.fac-card.is-active span{color:#eef7e0}

.features{left:0;top:970px;width:447px;height:256px;background:var(--dark)}
.features-title{color:var(--white)}
.features-sub{color:#aaa}
.feature{width:160px;padding-left:10px}
.feature::before{content:"";position:absolute;left:0;top:1px;width:4px;height:4px;border:0.6px solid #888;border-radius:50%}
.feature h5{font-size:5.5px;font-weight:600;color:var(--white)}
.feature p{margin-top:3px;font-size:4.3px;line-height:7px;color:#aaa}

.map-box{left:33px;top:1318px;width:380px;height:188px;background:var(--white);box-shadow:0 3px 12px rgba(0,0,0,.12)}
.map-list{position:absolute;left:0;top:0;width:91px;list-style:none}
.map-list li{position:absolute;left:10px;width:73px;font-size:4.5px;display:flex;justify-content:space-between}
.map-area{position:absolute;left:92px;top:3px;width:285px;height:182px;background:linear-gradient(135deg,#e9e9e9,#d9d9d9)}

.gal{top:1590px;width:95px;height:128px;background:linear-gradient(160deg,#41617f,#9aa69a 50%,#4c5d3c)}
.gal-caption{position:absolute;left:0;bottom:10px;width:95px;display:flex;justify-content:space-around;align-items:baseline}
.gal-caption small{font-size:4.5px;color:var(--white)}
.gal-caption b{font-size:8px;color:var(--green)}

.footer{left:0;top:1753px;width:447px;height:220px;background:var(--soft)}
.foot-logo{left:33px;top:1787px;font-weight:700;font-size:10px}
.foot-text{left:33px;top:1818px;width:115px;font-size:4.5px;line-height:7.5px;color:#555}
.foot-item{left:33px;width:120px;padding-left:9px;font-size:4.4px;line-height:6.5px;color:#555}
.foot-item b{color:var(--ink);font-weight:600}
.foot-item svg{position:absolute;left:0;top:1px;width:5px;height:6px}
.social{top:1924px;width:8px;height:8px;border-radius:50%}
.form-title{left:203px;top:1784px;font-size:15px}
.form-title b{font-weight:700}
.form-label{top:1812px;font-size:4.5px;font-weight:500}
.form-input{top:1821px;width:70px;height:15px;background:var(--white);font-size:4px;color:#999;padding:5px 7px}
.form-area{left:203px;top:1849px;width:211px;height:41px;background:var(--white);font-size:4px;color:#999;padding:6px 7px}
.btn-green{left:203px;top:1899px;width:47px;height:14px;background:var(--green);color:var(--white);font-size:4.5px;font-weight:700;display:flex;align-items:center;justify-content:center}
.foot-rule{left:33px;top:1948px;width:380px;height:.6px;background:#d6d6d6}
.to-top{left:422px;top:1941px;width:15px;height:15px;border-radius:50%;background:var(--green);color:var(--white);font-size:6px;display:flex;align-items:center;justify-content:center}
.copyright{left:0;width:447px;top:1959px;text-align:center;font-size:4.3px}

/* detail state */
.dim{left:0;top:0;width:447px;height:1973px;background:rgba(0,0,0,.34);z-index:5}
.modal{left:33px;top:575px;width:380px;height:212px;background:var(--white);z-index:6}
.modal > *{position:absolute}
.modal-close{left:375px;top:-16px;color:var(--white);font-size:10px}
.modal-title{left:18px;top:22px;font-size:14px}
.modal-title b{font-weight:700}
.spec-row{left:18px;width:124px;height:22px;border-bottom:.6px solid var(--line);display:flex;align-items:center;justify-content:space-between;font-size:4.5px;font-weight:600}
.spec-row span{display:flex;align-items:center;gap:5px}
.spec-row svg{width:9px;height:7px}
.badge{background:#eee;border-radius:50%;width:8px;height:8px;display:flex;align-items:center;justify-content:center;font-size:4px}
.badge-yes{background:#e4f2d2;color:var(--green-dark);border-radius:4px;padding:1px 4px;font-size:3.8px}
.modal-price{left:18px;top:163px;width:122px;height:17px;background:var(--green);color:var(--white);display:flex;align-items:center;justify-content:space-between;padding:0 14px;font-size:4.5px;font-weight:600}
.modal-price b{font-size:7.5px}
.floor-plan{left:167px;top:6px;width:207px;height:200px;background:linear-gradient(135deg,#e9f2fc,#dbe8f7)}
</style>
</head>
<body>
<main class="board">
  <svg class="board-waves" width="1413" height="2576" viewBox="0 0 1413 2576" aria-hidden="true">
    <path d="M0 2576 L0 1260 C 320 900 760 1700 1413 1150 L1413 2576 Z" fill="#9bce58"/>
    <path d="M0 2576 L0 1900 C 420 1500 900 1900 1413 1560 L1413 2576 Z" fill="#b3dc7e"/>
  </svg>

  <div class="brand">HIGH GROVE</div>
  <div class="brand-rule"></div>

  <h2 class="board-label" style="left:232px">HOME</h2>
  <h2 class="board-label" style="left:733px">APARTMENT DETAIL</h2>

  <!-- Home page -->
  <section class="site" style="left:233px">
    <header class="nav">
      <div class="nav-logo">HIGH GROVE</div>
      <ul class="nav-menu"><li>HIGH GROVE</li><li>THE PROJECT</li><li>APARTMENTS/SALES</li><li>LOCATION</li><li>GALLERY</li><li class="is-cta">CONTACT</li><li>ENG ▾</li></ul>
    </header>
    <div class="hero"></div>
    <div class="hero-panel"></div>
    <div class="hero-photo" role="img" aria-label="3D render of green terraced residential building"></div>
    <h1 class="hero-title">Sale Of Apartments<br>Directly From The investor<br>with <b>10% discount</b></h1>
    <p class="hero-price">Price from XXX EUR/m2</p>
    <div class="btn-dark">BUY NOW →</div>

    <div class="project-art" role="img" aria-label="Project presentation render cut into building silhouettes"></div>
    <h2 class="project-title">Project<br><b>Presentation</b></h2>
    <div class="accent project-accent"></div>
    <p class="project-text">Architecture, building materials – facades, roof, common areas etc.), information board (assignor, contractor, etc.), maintenance and management info, level of completion, etc.</p>

    <h2 class="sec-title" style="top:523px">Apartments/<b>Sales</b></h2>
    <div class="sec-accent" style="top:545px"></div>
    <p class="sec-sub" style="top:555px">Table with all apartments (70) – unit, floor, entrance/block, typology (1 bed, 2 beds, etc)</p>
    <div class="arrow-btn" style="left:12px;top:661px">‹</div>
    <div class="arrow-btn" style="left:426px;top:661px">›</div>
    <article class="apt-card" style="left:33px">
      <div class="apt-photo" role="img" aria-label="Apartment building exterior"></div>
      <span class="apt-tag">SALE</span><span class="apt-price">$320 000</span>
      <span class="apt-status">Available</span><h3 class="apt-name">One bed apartment</h3>
      <p class="apt-desc">Aenean sollicitudin, lorem quis bibendum auctor nisi elit consequat ipsum...</p>
      <div class="apt-specs"><span>⌗ 2450 sq</span><span>▭ 06</span><span>◡ 05</span><span>○ Yes</span></div>
      <span class="apt-view">View</span>
    </article>
    <article class="apt-card" style="left:162px">
      <div class="apt-photo" role="img" aria-label="Aerial view of apartment building"></div>
      <span class="apt-tag">SALE</span><span class="apt-price">$320 000</span>
      <span class="apt-status">Available</span><h3 class="apt-name">Two bed apartment</h3>
      <p class="apt-desc">Aenean sollicitudin, lorem quis bibendum auctor nisi elit consequat ipsum...</p>
      <div class="apt-specs"><span>⌗ 2450 sq</span><span>▭ 06</span><span>◡ 05</span><span>○ Yes</span></div>
      <span class="apt-view">View</span>
    </article>
    <article class="apt-card" style="left:291px">
      <div class="apt-photo" role="img" aria-label="White apartment block with greenery"></div>
      <span class="apt-tag">SALE</span><span class="apt-price">$320 000</span>
      <span class="apt-status">Available</span><h3 class="apt-name">Three bed apartment</h3>
      <p class="apt-desc">Aenean sollicitudin, lorem quis bibendum auctor nisi elit consequat ipsum...</p>
      <div class="apt-specs"><span>⌗ 2450 sq</span><span>▭ 06</span><span>◡ 05</span><span>○ Yes</span></div>
      <span class="apt-view">View</span>
    </article>

    <p class="layout-note">Map / Layout of the project with:</p>
    <h2 class="sec-title" style="top:816px">Facilities/<b>Benefits</b></h2>
    <div class="sec-accent" style="top:838px"></div>
    <p class="sec-sub" style="top:849px">Etiam rhoncus maecenas tempus tellus eget condim entum rhon cus sem quam semper</p>
    <div class="arrow-btn" style="left:12px;top:916px">‹</div>
    <div class="arrow-btn" style="left:426px;top:916px">›</div>
    <div class="fac-card" style="left:33px"><svg viewBox="0 0 20 20" fill="none" stroke="#333" stroke-width="1"><rect x="3" y="3" width="14" height="14" rx="2"/><rect x="6" y="9" width="8" height="4"/></svg><h4>Parking spaces</h4><p>Etiam rhoncus maecenas cus tempus tellus ul condim entum rhon cus...</p><span>→</span></div>
    <div class="fac-card" style="left:130px"><svg viewBox="0 0 20 20" fill="none" stroke="#333" stroke-width="1"><path d="M2 12 Q6 9 10 12 T18 12 M2 16 Q6 13 10 16 T18 16 M7 3 V11 M13 3 V11"/></svg><h4>Pool</h4><p>Etiam rhoncus maecenas cus tempus tellus ul condim entum rhon cus...</p><span>→</span></div>
    <div class="fac-card" style="left:227px"><svg viewBox="0 0 20 20" fill="none" stroke="#333" stroke-width="1"><rect x="2" y="2" width="6" height="8"/><circle cx="7" cy="15" r="3"/><circle cx="15" cy="15" r="3"/><path d="M7 15 L11 10 L15 15"/></svg><h4>Bicycle parking</h4><p>Etiam rhoncus maecenas cus tempus tellus ul condim entum rhon cus...</p><span>→</span></div>
    <div class="fac-card is-active" style="left:324px"><svg viewBox="0 0 20 20" fill="none" stroke="#fff" stroke-width="1"><path d="M3 13 A7 7 0 0 1 17 13 Z M2 15 H18 M10 4 V6"/></svg><h4>Restaurant</h4><p>Etiam rhoncus maecenas cus tempus tellus ul condim entum rhon cus...</p><span>→</span></div>

    <div class="features"></div>
    <h2 class="sec-title features-title" style="top:1016px">Construction/<b>Features</b></h2>
    <div class="sec-accent" style="top:1038px"></div>
    <p class="sec-sub features-sub" style="top:1047px">Etiam rhoncus maecenas tempus tellus eget condim entum rhon cus sem quam semper</p>
    <div class="feature" style="left:57px;top:1071px"><h5>Alvero Windows</h5><p>5 chamber noise reducing glazing with high temperature and noise insulation efficiency</p></div>
    <div class="feature" style="left:229px;top:1071px"><h5>Air conditioners</h5><p>All air conditioners piping systems are installed – ready to plug in the inside and outside body of the aircon system</p></div>
    <div class="feature" style="left:57px;top:1105px"><h5>Terrabrik bricks</h5><p>Austrian Terrabrik Thermobrik bricks with porous system and 25 cm thick outer walls</p></div>
    <div class="feature" style="left:229px;top:1105px"><h5>HPL ventilated facade</h5><p>Plakora GmbH – suspended ventilated facade with highly pressed laminated panels in wood color</p></div>
    <div class="feature" style="left:57px;top:1139px"><h5>High Ceilings</h5><p>2.70m high ceilings giving the light and space you need</p></div>
    <div class="feature" style="left:229px;top:1139px"><h5>Panoramic Vantis lifts</h5><p>Overlooking the park – giving you the everyday glimpse over the inside garden and putting a smile on your face</p></div>
    <div class="feature" style="left:57px;top:1172px"><h5>Thermal insulation</h5><p>System Termalux – silicone plaster thermal insulation system 10 cm thick and 15 cm thick from the north walls</p></div>
    <div class="feature" style="left:229px;top:1172px"><h5>Waterproofing with PVC</h5><p>Membrane Membrix – PVC membrane with high puncture and tear resistance, UV resistance and vapor permeability</p></div>

    <h2 class="sec-title" style="top:1261px">Our<b>Location</b></h2>
    <div class="sec-accent" style="top:1283px"></div>
    <p class="sec-sub" style="top:1292px;left:85px;width:277px">Neighborhood, local attractions, metro/bus stops, schools nearby, big shops etc.Maybe some sort of infographic with distance to the POI above.</p>
    <div class="map-box">
      <ul class="map-list">
        <li style="top:24px">Neighborhood<span>›</span></li>
        <li style="top:51px">Local attractions<span>›</span></li>
        <li style="top:77px">Landmarks<span>›</span></li>
        <li style="top:104px">Metro/bus stops<span>›</span></li>
        <li style="top:130px">Schools nearby<span>›</span></li>
        <li style="top:157px">Big shops<span>›</span></li>
      </ul>
      <div class="map-area" role="img" aria-label="Street map of the neighborhood with points of interest"></div>
    </div>

    <h2 class="sec-title" style="top:1539px">Our/<b>Gallery</b></h2>
    <div class="sec-accent" style="top:1561px"></div>
    <p class="sec-sub" style="top:1571px">Boxes for each month with photos of the construction progress</p>
    <div class="gal" style="left:77px" role="img" aria-label="Construction progress photo"><div class="gal-caption"><small>April 2021</small><b>View</b></div></div>
    <div class="gal" style="left:177px" role="img" aria-label="Construction site with scaffolding"><div class="gal-caption"><small>April 2021</small><b>View</b></div></div>
    <div class="gal" style="left:276px" role="img" aria-label="Finished building facade"><div class="gal-caption"><small>April 2021</small><b>View</b></div></div>

    <footer class="footer"></footer>
    <div class="foot-logo">HIGH GROVE</div>
    <p class="foot-text">Please select a topic below related to your inquiry. If you don't find what you need, fill out our contact form.</p>
    <div class="foot-item" style="top:1851px"><svg viewBox="0 0 5 6"><path d="M2.5 6 L0.5 2.5 A2 2 0 1 1 4.5 2.5 Z" fill="#8cc63f"/></svg><b>Location*</b><br>Some address goes here city name country name</div>
    <div class="foot-item" style="top:1877px"><svg viewBox="0 0 5 6"><path d="M1 0.5 L2 2 L1.5 3 Q2.5 4.5 3.5 4.5 L4.5 4 L4.8 5.5 Q2 6 0.5 1.5 Z" fill="#8cc63f"/></svg><b>Phone*</b><br>Call Us: +08 321 654 0987</div>
    <div class="foot-item" style="top:1896px"><svg viewBox="0 0 5 6"><rect x="0" y="1.5" width="5" height="3.5" fill="#8cc63f"/></svg><b>Email*</b><br>info@highgrove-homes.com</div>
    <div class="social" style="left:33px;background:#3b5998"></div>
    <div class="social" style="left:44px;background:#38a1f3"></div>
    <h2 class="form-title">Contact <b>Form</b></h2>
    <span class="form-label" style="left:203px">Name*</span>
    <span class="form-label" style="left:275px">Email*</span>
    <span class="form-label" style="left:345px">Phone*</span>
    <div class="form-input" style="left:203px">Enter your name</div>
    <div class="form-input" style="left:275px;width:68px">Enter your email</div>
    <div class="form-input" style="left:345px">Enter your phone</div>
    <span class="form-label" style="left:203px;top:1842px">Message*</span>
    <div class="form-area">Type your text</div>
    <div class="btn-green">SUBMIT</div>
    <div class="foot-rule"></div>
    <div class="to-top">↑</div>
    <p class="copyright">© Copyright 2021 High Grove All Rights Reserved</p>
  </section>

  <!-- Apartment detail state -->
  <section class="site" style="left:733px">
    <header class="nav">
      <div class="nav-logo">HIGH GROVE</div>
      <ul class="nav-menu"><li>HIGH GROVE</li><li>THE PROJECT</li><li>APARTMENTS/SALES</li><li>LOCATION</li><li>GALLERY</li><li class="is-cta">CONTACT</li><li>ENG ▾</li></ul>
    </header>
    <div class="hero"></div>
    <div class="hero-panel"></div>
    <div class="hero-photo" role="img" aria-label="3D render of green terraced residential building"></div>
    <h1 class="hero-title">Sale Of Apartments<br>Directly From The investor<br>with <b>10% discount</b></h1>
    <p class="hero-price">Price from XXX EUR/m2</p>
    <div class="btn-dark">BUY NOW →</div>

    <div class="project-art" role="img" aria-label="Project presentation render cut into building silhouettes"></div>
    <h2 class="project-title">Project<br><b>Presentation</b></h2>
    <div class="accent project-accent"></div>
    <p class="project-text">Architecture, building materials – facades, roof, common areas etc.), information board (assignor, contractor, etc.), maintenance and management info, level of completion, etc.</p>

    <h2 class="sec-title" style="top:523px">Apartments/<b>Sales</b></h2>
    <div class="sec-accent" style="top:545px"></div>
    <p class="sec-sub" style="top:555px">Table with all apartments (70) – unit, floor, entrance/block, typology (1 bed, 2 beds, etc)</p>
    <div class="arrow-btn" style="left:12px;top:661px">‹</div>
    <div class="arrow-btn" style="left:426px;top:661px">›</div>

    <p class="layout-note">Map / Layout of the project with:</p>
    <h2 class="sec-title" style="top:816px">Facilities/<b>Benefits</b></h2>
    <div class="sec-accent" style="top:838px"></div>
    <p class="sec-sub" style="top:849px">Etiam rhoncus maecenas tempus tellus eget condim entum rhon cus sem quam semper</p>
    <div class="arrow-btn" style="left:12px;top:916px">‹</div>
    <div class="arrow-btn" style="left:426px;top:916px">›</div>
    <div class="fac-card" style="left:33px"><svg viewBox="0 0 20 20" fill="none" stroke="#333" stroke-width="1"><rect x="3" y="3" width="14" height="14" rx="2"/><rect x="6" y="9" width="8" height="4"/></svg><h4>Parking spaces</h4><p>Etiam rhoncus maecenas cus tempus tellus ul condim entum rhon cus...</p><span>→</span></div>
    <div class="fac-card" style="left:130px"><svg viewBox="0 0 20 20" fill="none" stroke="#333" stroke-width="1"><path d="M2 12 Q6 9 10 12 T18 12 M2 16 Q6 13 10 16 T18 16 M7 3 V11 M13 3 V11"/></svg><h4>Pool</h4><p>Etiam rhoncus maecenas cus tempus tellus ul condim entum rhon cus...</p><span>→</span></div>
    <div class="fac-card" style="left:227px"><svg viewBox="0 0 20 20" fill="none" stroke="#333" stroke-width="1"><rect x="2" y="2" width="6" height="8"/><circle cx="7" cy="15" r="3"/><circle cx="15" cy="15" r="3"/><path d="M7 15 L11 10 L15 15"/></svg><h4>Bicycle parking</h4><p>Etiam rhoncus maecenas cus tempus tellus ul condim entum rhon cus...</p><span>→</span></div>
    <div class="fac-card is-active" style="left:324px"><svg viewBox="0 0 20 20" fill="none" stroke="#fff" stroke-width="1"><path d="M3 13 A7 7 0 0 1 17 13 Z M2 15 H18 M10 4 V6"/></svg><h4>Restaurant</h4><p>Etiam rhoncus maecenas cus tempus tellus ul condim entum rhon cus...</p><span>→</span></div>

    <div class="features"></div>
    <h2 class="sec-title features-title" style="top:1016px">Construction/<b>Features</b></h2>
    <div class="sec-accent" style="top:1038px"></div>
    <p class="sec-sub features-sub" style="top:1047px">Etiam rhoncus maecenas tempus tellus eget condim entum rhon cus sem quam semper</p>
    <div class="feature" style="left:57px;top:1071px"><h5>Alvero Windows</h5><p>5 chamber noise reducing glazing with high temperature and noise insulation efficiency</p></div>
    <div class="feature" style="left:229px;top:1071px"><h5>Air conditioners</h5><p>All air conditioners piping systems are installed – ready to plug in the inside and outside body of the aircon system</p></div>
    <div class="feature" style="left:57px;top:1105px"><h5>Terrabrik bricks</h5><p>Austrian Terrabrik Thermobrik bricks with porous system and 25 cm thick outer walls</p></div>
    <div class="feature" style="left:229px;top:1105px"><h5>HPL ventilated facade</h5><p>Plakora GmbH – suspended ventilated facade with highly pressed laminated panels in wood color</p></div>
    <div class="feature" style="left:57px;top:1139px"><h5>High Ceilings</h5><p>2.70m high ceilings giving the light and space you need</p></div>
    <div class="feature" style="left:229px;top:1139px"><h5>Panoramic Vantis lifts</h5><p>Overlooking the park – giving you the everyday glimpse over the inside garden and putting a smile on your face</p></div>
    <div class="feature" style="left:57px;top:1172px"><h5>Thermal insulation</h5><p>System Termalux – silicone plaster thermal insulation system 10 cm thick and 15 cm thick from the north walls</p></div>
    <div class="feature" style="left:229px;top:1172px"><h5>Waterproofing with PVC</h5><p>Membrane Membrix – PVC membrane with high puncture and tear resistance, UV resistance and vapor permeability</p></div>

    <h2 class="sec-title" style="top:1261px">Our<b>Location</b></h2>
    <div class="sec-accent" style="top:1283px"></div>
    <p class="sec-sub" style="top:1292px;left:85px;width:277px">Neighborhood, local attractions, metro/bus stops, schools nearby, big shops etc.Maybe some sort of infographic with distance to the POI above.</p>
    <div class="map-box">
      <ul class="map-list">
        <li style="top:24px">Neighborhood<span>›</span></li>
        <li style="top:51px">Local attractions<span>›</span></li>
        <li style="top:77px">Landmarks<span>›</span></li>
        <li style="top:104px">Metro/bus stops<span>›</span></li>
        <li style="top:130px">Schools nearby<span>›</span></li>
        <li style="top:157px">Big shops<span>›</span></li>
      </ul>
      <div class="map-area" role="img" aria-label="Street map of the neighborhood with points of interest"></div>
    </div>

    <h2 class="sec-title" style="top:1539px">Our/<b>Gallery</b></h2>
    <div class="sec-accent" style="top:1561px"></div>
    <p class="sec-sub" style="top:1571px">Boxes for each month with photos of the construction progress</p>
    <div class="gal" style="left:77px" role="img" aria-label="Construction progress photo"><div class="gal-caption"><small>April 2021</small><b>View</b></div></div>
    <div class="gal" style="left:177px" role="img" aria-label="Construction site with scaffolding"><div class="gal-caption"><small>April 2021</small><b>View</b></div></div>
    <div class="gal" style="left:276px" role="img" aria-label="Finished building facade"><div class="gal-caption"><small>April 2021</small><b>View</b></div></div>

    <footer class="footer"></footer>
    <div class="foot-logo">HIGH GROVE</div>
    <p class="foot-text">Please select a topic below related to your inquiry. If you don't find what you need, fill out our contact form.</p>
    <div class="foot-item" style="top:1851px"><svg viewBox="0 0 5 6"><path d="M2.5 6 L0.5 2.5 A2 2 0 1 1 4.5 2.5 Z" fill="#8cc63f"/></svg><b>Location*</b><br>Some address goes here city name country name</div>
    <div class="foot-item" style="top:1877px"><svg viewBox="0 0 5 6"><path d="M1 0.5 L2 2 L1.5 3 Q2.5 4.5 3.5 4.5 L4.5 4 L4.8 5.5 Q2 6 0.5 1.5 Z" fill="#8cc63f"/></svg><b>Phone*</b><br>Call Us: +08 321 654 0987</div>
    <div class="foot-item" style="top:1896px"><svg viewBox="0 0 5 6"><rect x="0" y="1.5" width="5" height="3.5" fill="#8cc63f"/></svg><b>Email*</b><br>info@highgrove-homes.com</div>
    <div class="social" style="left:33px;background:#3b5998"></div>
    <div class="social" style="left:44px;background:#38a1f3"></div>
    <h2 class="form-title">Contact <b>Form</b></h2>
    <span class="form-label" style="left:203px">Name*</span>
    <span class="form-label" style="left:275px">Email*</span>
    <span class="form-label" style="left:345px">Phone*</span>
    <div class="form-input" style="left:203px">Enter your name</div>
    <div class="form-input" style="left:275px;width:68px">Enter your email</div>
    <div class="form-input" style="left:345px">Enter your phone</div>
    <span class="form-label" style="left:203px;top:1842px">Message*</span>
    <div class="form-area">Type your text</div>
    <div class="btn-green">SUBMIT</div>
    <div class="foot-rule"></div>
    <div class="to-top">↑</div>
    <p class="copyright">© Copyright 2021 High Grove All Rights Reserved</p>

    <div class="dim"></div>
    <div class="modal">
      <span class="modal-close">×</span>
      <h3 class="modal-title">Apartment <b>A12</b></h3>
      <div class="spec-row" style="top:52px"><span><svg viewBox="0 0 9 7" fill="none" stroke="#555" stroke-width=".6"><rect x=".5" y="2" width="8" height="4"/><path d="M.5 4 H8.5"/></svg>Bedrooms</span><i class="badge">6</i></div>
      <div class="spec-row" style="top:74px"><span><svg viewBox="0 0 9 7" fill="none" stroke="#555" stroke-width=".6"><path d="M.5 3 H8.5 Q8 6 4.5 6 Q1 6 .5 3 Z"/></svg>Bathrooms</span><i class="badge">4</i></div>
      <div class="spec-row" style="top:96px"><span><svg viewBox="0 0 9 7" fill="none" stroke="#555" stroke-width=".6"><rect x=".5" y=".5" width="8" height="6"/></svg>Total Area SQ.Feet</span><span>2450 sq</span></div>
      <div class="spec-row" style="top:118px"><span><svg viewBox="0 0 9 7" fill="none" stroke="#555" stroke-width=".6"><circle cx="2.5" cy="5" r="1.5"/><circle cx="6.5" cy="5" r="1.5"/></svg>Parking</span><i class="badge-yes">YES</i></div>
      <div class="spec-row" style="top:140px"><span><svg viewBox="0 0 9 7" fill="none" stroke="#555" stroke-width=".6"><path d="M.5 5 Q2.5 3.5 4.5 5 T8.5 5 M3 .5 V4 M6 .5 V4"/></svg>Swimming Pool</span><i class="badge-yes">YES</i></div>
      <div class="modal-price"><span>Price</span><b>$78,4500</b></div>
      <div class="floor-plan" role="img" aria-label="Floor plan drawing of apartment A12"></div>
    </div>
  </section>
</main>
</body>
</html>
```